Steady Hands, professional newsletter for GAPM

** updated based on results so far** We need a 2 page newsletter designed on both sides of an 8.6 x 11 sheet back and front. Page one needs our logo below, name steady hands in large letters tagline of official newsletter of the guild of acute practice medicine volume and issue number locations It needs to include five locations for 250-400 word articles each with a spot for a picture. Page 2 needs to include contact information including address, phone number, email, twitter and facebook info below. The design need to complement out log in color, be professional with clean lines and easy to follow. We are a non profit organization dedicated to providers of urgent care medicine.

Target Market(s)

Physicians, Nurse Practitioners, Physician Assistants

Requirements
Must have
• 2 pages, back and front 8.5x 11
• 5 article area 250-400 words, one image for each
• our logo
• Name: Steady Hands - page one large visible print
• Contact inf:
• Guild of Acute Practice Medicine
• 912 Larkmoor Ave. Suite 418E
• Brookfell, IL 60498
• 1 855-314-7093
• Info@gaopm.org
• @GuildAPM
Nice to have
• ease of entering info
• professional clean lines

```html
<!DOCTYPE html>
<html lang="en">
<head>
<meta charset="utf-8">
<title>Steady Hands — Newsletter of the Guild of Acute Practice Medicine</title>
<link href="https://fonts.googleapis.com/css2?family=Open+Sans:wght@400;600;700;800&display=swap" rel="stylesheet">
<style>
  :root {
    --orange: #eea431;
    --orange-deep: #e8952a;
    --red: #b93a24;
    --blue: #3a74b4;
    --blue-soft: #a9c3e0;
    --ink: #4a4a4a;
    --ink-soft: #6b6b6b;
    --paper: #ffffff;
    --backdrop: #e7e7e7;
    --map-a: #dfe6d6;
    --map-b: #c9d7e3;
  }
  * { box-sizing: border-box; margin: 0; padding: 0; }
  html, body { width: 1200px; height: 1200px; overflow: hidden; background: var(--backdrop); }
  body { font-family: "Open Sans", Arial, sans-serif; color: var(--ink); }

  .canvas { position: relative; width: 1200px; height: 1200px; overflow: hidden; }

  .page {
    position: absolute;
    background: var(--paper);
    overflow: hidden;
    box-shadow: 0 2px 10px rgba(0,0,0,0.12);
  }

  /* ---------- Shared ---------- */
  .placeholder {
    background: var(--blue);
    color: #fff;
    display: flex;
    flex-direction: column;
    align-items: center;
    justify-content: center;
    text-align: center;
  }
  .placeholder .ph-title { font-weight: 600; line-height: 1.1; }
  .placeholder .ph-sub { color: var(--blue-soft); font-weight: 400; }

  .brand { display: flex; align-items: center; gap: 6px; }
  .brand .brand-dot { border-radius: 50%; background: var(--orange); flex: none; }
  .brand .brand-name {
    color: var(--ink-soft);
    font-weight: 400;
    text-transform: uppercase;
    letter-spacing: 0.06em;
    line-height: 1.25;
  }

  /* ---------- Front cover ---------- */
  .cover { left: 240px; top: 20px; width: 340px; height: 440px; }
  .cover .topbar {
    height: 18px;
    background: var(--orange);
    display: flex;
    align-items: center;
    justify-content: space-between;
    padding: 0 12px;
    color: #fff;
    font-size: 5.5px;
    font-weight: 700;
    letter-spacing: 0.08em;
  }
  .cover .masthead {
    color: var(--orange-deep);
    font-weight: 800;
    font-size: 41px;
    letter-spacing: -0.5px;
    line-height: 1;
    padding: 12px 12px 0;
    white-space: nowrap;
  }
  .cover .brand { justify-content: flex-end; padding: 6px 18px 6px 0; }
  .cover .brand .brand-dot { width: 12px; height: 12px; }
  .cover .brand .brand-name { font-size: 5.5px; width: 80px; }
  .cover .tagline {
    position: relative;
    height: 14px;
    background: var(--orange);
    color: #fff;
    font-size: 5.2px;
    font-weight: 700;
    letter-spacing: 0.05em;
    display: flex;
    align-items: center;
    padding-left: 12px;
  }
  .cover .tagline svg { position: absolute; right: 0; top: 0; }
  .cover .body { display: flex; gap: 14px; padding: 12px 14px 0; }
  .cover .col-text { width: 168px; }
  .cover h2 {
    font-size: 5.8px;
    font-weight: 700;
    color: var(--ink);
    letter-spacing: 0.02em;
    margin: 0 0 4px;
  }
  .cover h2.next { margin-top: 8px; }
  .cover p {
    font-size: 5.2px;
    line-height: 1.45;
    color: var(--ink-soft);
    margin-bottom: 4px;
    text-align: justify;
  }
  .cover .placeholder { width: 128px; height: 128px; margin-top: 40px; flex: none; }
  .cover .placeholder .ph-title { font-size: 12px; }
  .cover .placeholder .ph-sub { font-size: 7px; }
  .cover .footstrip { position: absolute; left: 0; bottom: 0; }

  /* ---------- Back cover ---------- */
  .back { left: 620px; top: 20px; width: 340px; height: 440px; }
  .back .contact-band {
    position: absolute;
    left: 0; top: 56px;
    width: 100%; height: 24px;
    background: var(--orange);
    color: #fff;
    font-weight: 600;
    font-size: 12px;
    letter-spacing: 0.04em;
    display: flex;
    align-items: center;
    justify-content: center;
  }
  .back .brand { position: absolute; left: 0; right: 0; top: 104px; justify-content: center; }
  .back .brand .brand-dot { width: 16px; height: 16px; }
  .back .brand .brand-name { font-size: 7px; width: 112px; }
  .back .map {
    position: absolute;
    left: 20px; top: 172px;
    width: 130px; height: 110px;
    background: linear-gradient(135deg, var(--map-a), var(--map-b));
  }
  .back .contact-list { position: absolute; left: 164px; top: 178px; list-style: none; }
  .back .contact-list li {
    display: flex;
    align-items: flex-start;
    gap: 7px;
    font-size: 6.2px;
    line-height: 1.45;
    color: var(--ink-soft);
    margin-bottom: 8px;
  }
  .back .contact-list svg { flex: none; margin-top: 1px; }
  .back .footstrip { position: absolute; left: 0; top: 336px; }

  /* ---------- Inner spread ---------- */
  .spread-page { top: 490px; width: 520px; height: 673px; }
  .spread-left { left: 80px; }
  .spread-right { left: 600px; border-left: 1px solid #e4e4e4; }
  .spread-page .content { padding: 24px 24px 0; }
  .spread-page p {
    font-size: 7.4px;
    line-height: 1.5;
    color: var(--ink-soft);
    margin-bottom: 7px;
    text-align: justify;
  }
  .spread-page h2 {
    font-size: 9.4px;
    font-weight: 600;
    color: var(--ink);
    letter-spacing: 0.01em;
    margin: 12px 0 8px;
  }
  .spread-page h2.first { margin-top: 0; }
  .article-row { display: flex; gap: 10px; align-items: flex-start; }
  .article-row .col { flex: 1; }
  .spread-page .placeholder { flex: none; }
  .spread-page .placeholder .ph-title { font-size: 15px; }
  .spread-page .placeholder .ph-sub { font-size: 8.5px; margin-top: 2px; }
  .ph-md { width: 180px; height: 130px; }
  .ph-lg { width: 205px; height: 166px; }
  .ph-sq { width: 215px; height: 167px; }

  .page-footer { position: absolute; left: 0; bottom: 0; width: 100%; height: 15px; }
  .page-footer svg { position: absolute; left: 0; top: 0; }
  .page-footer .foot-label {
    position: absolute;
    top: 0; height: 15px;
    display: flex; align-items: center;
    color: #fff;
    font-size: 7.2px;
    font-weight: 600;
    letter-spacing: 0.04em;
  }
  .page-footer .foot-org { left: 24px; }
  .page-footer .foot-issue { right: 24px; }
</style>
</head>
<body>
<div class="canvas">

  <!-- Front cover -->
  <section class="page cover">
    <div class="topbar"><span>VOLUME - 01 | ISSUE - 001</span><span>WWW.GAOPM.ORG</span></div>
    <h1 class="masthead">STEADY HANDS</h1>
    <div class="brand">
      <span class="brand-dot"></span>
      <span class="brand-name">Guild of Acute Practice Medicine</span>
    </div>
    <div class="tagline">
      OFFICIAL NEWSLETTER OF THE GUILD OF ACUTE PRACTICE MEDICINE
      <svg width="40" height="14" viewBox="0 0 40 14"><polygon points="14,0 40,0 40,14 0,14" fill="var(--red)"/></svg>
    </div>
    <div class="body">
      <div class="col-text">
        <h2>THIS IS DUMMY TITLE 01 GENERATED</h2>
        <p>Lorem ipsum dolor sit amet, consectetuer adipiscing elit. Aenean commodo ligula eget dolor. Aenean massa. Cum sociis natoque penatibus et magnis dis parturient montes.</p>
        <p>Donec quam felis, ultricies nec, pellentesque eu, pretium quis, sem. Nulla consequat massa quis enim. Donec pede justo, fringilla vel, aliquet nec, vulputate eget, arcu.</p>
        <p>Aenean vulputate eleifend tellus. Aenean leo ligula, porttitor eu, consequat vitae, eleifend ac, enim. Aliquam lorem ante, dapibus in, viverra quis, feugiat a, tellus.</p>
        <h2 class="next">THIS IS DUMMY TITLE 02 GENERATED</h2>
        <p>Lorem ipsum dolor sit amet, consectetuer adipiscing elit. Aenean commodo ligula eget dolor. Aenean massa. Cum sociis natoque penatibus et magnis dis parturient montes, nascetur ridiculus mus.</p>
        <p>Vivamus elementum semper nisi. Aenean vulputate eleifend tellus. Quisque rutrum. Aenean imperdiet. Etiam ultricies nisi vel augue. Curabitur ullamcorper ultricies nisi.</p>
      </div>
      <div class="placeholder" role="img" aria-label="Article photo for the first story">
        <span class="ph-title">Placeholder Image</span>
        <span class="ph-sub">Lorem Ipsum</span>
      </div>
    </div>
    <svg class="footstrip" width="340" height="12" viewBox="0 0 340 12">
      <rect x="0" y="0" width="340" height="12" fill="var(--orange)"/>
      <polygon points="230,0 340,0 340,12 218,12" fill="var(--red)"/>
    </svg>
  </section>

  <!-- Back cover -->
  <section class="page back">
    <div class="contact-band">CONTACT US</div>
    <div class="brand">
      <span class="brand-dot"></span>
      <span class="brand-name">Guild of Acute Practice Medicine</span>
    </div>
    <div class="map" role="img" aria-label="Street map showing the guild office location"></div>
    <ul class="contact-list">
      <li>
        <svg width="8" height="10" viewBox="0 0 8 10"><path d="M4 0a4 4 0 0 0-4 4c0 3 4 6 4 6s4-3 4-6a4 4 0 0 0-4-4z" fill="var(--orange)"/><circle cx="4" cy="4" r="1.4" fill="#fff"/></svg>
        <span>912 Larkmoor Ave. Suite 418E<br>Brookfell, IL 60498</span>
      </li>
      <li>
        <svg width="8" height="8" viewBox="0 0 8 8"><path d="M1.5 0.5l1.5 1.8-0.8 1.1a5 5 0 0 0 2.4 2.4l1.1-0.8 1.8 1.5-0.9 1.2C3.6 7.6 0.4 4.4 0.3 1.4z" fill="var(--orange)"/></svg>
        <span>1 855-314-7093</span>
      </li>
      <li>
        <svg width="9" height="7" viewBox="0 0 9 7"><rect x="0" y="0" width="9" height="7" rx="1" fill="var(--orange)"/><polyline points="0.5,0.8 4.5,4 8.5,0.8" fill="none" stroke="#fff" stroke-width="0.8"/></svg>
        <span>Info@gaopm.org</span>
      </li>
      <li>
        <svg width="8" height="8" viewBox="0 0 8 8"><circle cx="4" cy="4" r="4" fill="var(--orange)"/></svg>
        <span>www.gaopm.org</span>
      </li>
      <li>
        <svg width="8" height="8" viewBox="0 0 8 8"><circle cx="4" cy="4" r="4" fill="var(--blue)"/></svg>
        <span>@GuildAPM</span>
      </li>
    </ul>
    <svg class="footstrip" width="340" height="32" viewBox="0 0 340 32">
      <polygon points="0,0 36,0 58,32 0,32" fill="var(--red)"/>
      <polygon points="36,0 340,0 340,32 58,32" fill="var(--orange)"/>
    </svg>
  </section>

  <!-- Inner spread, left page -->
  <section class="page spread-page spread-left">
    <div class="content">
      <div class="article-row">
        <div class="col">
          <p>Nam quam nunc, blandit vel, luctus pulvinar, hendrerit id, lorem. Maecenas nec odio et ante tincidunt tempus. Donec vitae sapien ut libero venenatis faucibus. Nullam quis ante. Etiam sit amet orci eget eros faucibus tincidunt. Duis leo. Sed fringilla mauris sit amet nibh. Donec sodales sagittis magna.</p>
          <p>Sed consequat, leo eget bibendum sodales, augue velit cursus nunc, quis gravida magna mi a libero. Fusce vulputate eleifend sapien. Vestibulum purus quam, scelerisque ut, mollis sed, nonummy id, metus. Nullam accumsan lorem in dui. Cras ultricies mi eu turpis hendrerit fringilla. Vestibulum ante ipsum primis in faucibus orci luctus et ultrices posuere cubilia Curae.</p>
        </div>
        <div class="placeholder ph-md" role="img" aria-label="Article photo continuing the second story">
          <span class="ph-title">Placeholder Image</span>
          <span class="ph-sub">Lorem Ipsum</span>
        </div>
      </div>

      <h2>THIS IS DUMMY TITLE 03 GENERATED</h2>
      <div class="article-row">
        <div class="placeholder ph-lg" role="img" aria-label="Article photo for the third story">
          <span class="ph-title">Placeholder Image</span>
          <span class="ph-sub">Lorem Ipsum</span>
        </div>
        <div class="col">
          <p>Lorem ipsum dolor sit amet, consectetuer adipiscing elit. Aenean commodo ligula eget dolor. Aenean massa. Cum sociis natoque penatibus et magnis dis parturient montes, nascetur ridiculus mus. Donec quam felis, ultricies nec, pellentesque eu, pretium quis, sem.</p>
          <p>Nulla consequat massa quis enim. Donec pede justo, fringilla vel, aliquet nec, vulputate eget, arcu. In enim justo, rhoncus ut, imperdiet a, venenatis vitae, justo. Nullam dictum felis eu pede mollis pretium. Integer tincidunt. Cras dapibus. Vivamus elementum semper nisi.</p>
          <p>Aenean vulputate eleifend tellus. Aenean leo ligula, porttitor eu, consequat vitae, eleifend ac, enim. Aliquam lorem ante, dapibus in, viverra quis, feugiat a, tellus. Phasellus viverra nulla ut metus varius laoreet. Quisque rutrum. Aenean imperdiet.</p>
        </div>
      </div>

      <p>Curabitur ullamcorper ultricies nisi. Nam eget dui. Etiam rhoncus. Maecenas tempus, tellus eget condimentum rhoncus, sem quam semper libero, sit amet adipiscing sem neque sed ipsum. Nam quam nunc, blandit vel, luctus pulvinar, hendrerit id, lorem. Maecenas nec odio et ante tincidunt tempus. Donec vitae sapien ut libero venenatis faucibus. Nullam quis ante. Etiam sit amet orci eget eros faucibus tincidunt. Duis leo. Sed fringilla mauris sit amet nibh. Donec sodales sagittis magna.</p>
      <p>Fusce vulputate eleifend sapien. Vestibulum purus quam, scelerisque ut, mollis sed, nonummy id, metus. Nullam accumsan lorem in dui. Cras ultricies mi eu turpis hendrerit fringilla. Vestibulum ante ipsum primis in faucibus orci luctus et ultrices posuere cubilia Curae; In ac dui quis mi consectetuer lacinia. Nam pretium turpis et arcu. Duis arcu tortor, suscipit eget, imperdiet nec, imperdiet iaculis, ipsum. Sed aliquam ultrices mauris. Integer ante arcu, accumsan a, consectetuer eget, posuere ut, mauris.</p>
      <p>Praesent adipiscing. Phasellus ullamcorper ipsum rutrum nunc. Nunc nonummy metus. Vestibulum volutpat pretium libero. Cras id dui. Aenean ut eros et nisl sagittis vestibulum. Nullam nulla eros, ultricies sit amet, nonummy id, imperdiet feugiat, pede. Sed lectus. Donec mollis hendrerit risus. Phasellus nec sem in justo pellentesque facilisis. Etiam imperdiet imperdiet orci. Nunc nec neque. Phasellus leo dolor, tempus non, auctor et, hendrerit quis, nisi. Curabitur ligula sapien, tincidunt non, euismod vitae, posuere imperdiet, leo.</p>
      <p>Maecenas malesuada. Praesent congue erat at massa. Sed cursus turpis vitae tortor. Donec posuere vulputate arcu. Phasellus accumsan cursus velit. Vestibulum ante ipsum primis in faucibus orci luctus et ultrices posuere cubilia Curae; Sed aliquam, nisi quis porttitor congue, elit erat euismod orci.</p>
    </div>
    <footer class="page-footer">
      <svg width="520" height="15" viewBox="0 0 520 15">
        <rect x="0" y="0" width="520" height="15" fill="var(--orange)"/>
        <polygon points="282,0 520,0 520,15 270,15" fill="var(--red)"/>
      </svg>
      <span class="foot-label foot-org">GUILD OF ACUTE PRACTICE MEDICINE</span>
      <span class="foot-label foot-issue">VOLUME - 01 &nbsp;|&nbsp; ISSUE - 001</span>
    </footer>
  </section>

  <!-- Inner spread, right page -->
  <section class="page spread-page spread-right">
    <div class="content">
      <h2 class="first">THIS IS DUMMY TITLE 04 GENERATED</h2>
      <div class="article-row">
        <div class="col">
          <p>Lorem ipsum dolor sit amet, consectetuer adipiscing elit. Aenean commodo ligula eget dolor. Aenean massa. Cum sociis natoque penatibus et magnis dis parturient montes, nascetur ridiculus mus.</p>
          <p>Donec quam felis, ultricies nec, pellentesque eu, pretium quis, sem. Nulla consequat massa quis enim. Donec pede justo, fringilla vel, aliquet nec, vulputate eget, arcu. In enim justo, rhoncus ut, imperdiet a, venenatis vitae, justo. Nullam dictum felis eu pede mollis pretium. Integer tincidunt. Cras dapibus. Vivamus elementum semper nisi. Aenean vulputate eleifend tellus. Aenean leo ligula, porttitor eu, consequat vitae, eleifend ac, enim.</p>
        </div>
        <div class="placeholder ph-lg" role="img" aria-label="Article photo for the fourth story">
          <span class="ph-title">Placeholder Image</span>
          <span class="ph-sub">Lorem Ipsum</span>
        </div>
      </div>
      <p>Aliquam lorem ante, dapibus in, viverra quis, feugiat a, tellus. Phasellus viverra nulla ut metus varius laoreet. Quisque rutrum. Aenean imperdiet. Etiam ultricies nisi vel augue. Curabitur ullamcorper ultricies nisi. Nam eget dui. Etiam rhoncus. Maecenas tempus, tellus eget condimentum rhoncus, sem quam semper libero, sit amet adipiscing sem neque sed ipsum. Nam quam nunc, blandit vel, luctus pulvinar, hendrerit id, lorem. Maecenas nec odio et ante tincidunt tempus. Donec vitae sapien ut libero venenatis faucibus. Nullam quis ante. Etiam sit amet orci eget eros faucibus tincidunt.</p>
      <p>Duis leo. Sed fringilla mauris sit amet nibh. Donec sodales sagittis magna. Sed consequat, leo eget bibendum sodales, augue velit cursus nunc, quis gravida magna mi a libero. Fusce vulputate eleifend sapien. Vestibulum purus quam, scelerisque ut, mollis sed, nonummy id, metus. Nullam accumsan lorem in dui. Cras ultricies mi eu turpis hendrerit fringilla. Vestibulum ante ipsum primis in faucibus orci luctus et ultrices posuere cubilia Curae; In ac dui quis mi consectetuer lacinia. Nam pretium turpis et arcu. Sed aliquam ultrices mauris. Integer ante arcu, accumsan.</p>

      <h2>THIS IS DUMMY TITLE 05 GENERATED</h2>
      <div class="article-row">
        <div class="placeholder ph-sq" role="img" aria-label="Article photo for the fifth story">
          <span class="ph-title">Placeholder Image</span>
          <span class="ph-sub">Lorem Ipsum</span>
        </div>
        <div class="col">
          <p>Lorem ipsum dolor sit amet, consectetuer adipiscing elit. Aenean commodo ligula eget dolor. Aenean massa. Cum sociis natoque penatibus et magnis dis parturient montes, nascetur ridiculus mus.</p>
          <p>Donec quam felis, ultricies nec, pellentesque eu, pretium quis, sem. Nulla consequat massa quis enim. Donec pede justo, fringilla vel, aliquet nec, vulputate eget, arcu. In enim justo, rhoncus ut, imperdiet a, venenatis vitae, justo. Nullam dictum felis eu pede mollis pretium. Integer tincidunt. Cras dapibus.</p>
          <p>Vivamus elementum semper nisi. Aenean vulputate eleifend tellus. Aenean leo ligula, porttitor eu, consequat vitae, eleifend ac, enim. Aliquam lorem ante, dapibus in, viverra quis, feugiat a, tellus. Phasellus viverra nulla ut metus varius laoreet.</p>
        </div>
      </div>
      <p>Curabitur ullamcorper ultricies nisi. Nam eget dui. Etiam rhoncus. Maecenas tempus, tellus eget condimentum rhoncus, sem quam semper libero, sit amet adipiscing sem neque sed ipsum. Nam quam nunc, blandit vel, luctus pulvinar, hendrerit id.</p>
      <p>Maecenas nec odio et ante tincidunt tempus. Donec vitae sapien ut libero venenatis faucibus. Nullam quis ante. Etiam sit amet orci eget eros faucibus tincidunt. Duis leo. Sed fringilla mauris sit amet nibh. Donec sodales sagittis magna. Sed consequat, leo eget bibendum sodales, augue velit cursus nunc, quis gravida magna mi a libero. Fusce vulputate eleifend sapien. Cras ultricies mi eu turpis hendrerit fringilla.</p>
    </div>
    <footer class="page-footer">
      <svg width="520" height="15" viewBox="0 0 520 15">
        <rect x="0" y="0" width="520" height="15" fill="var(--orange)"/>
        <polygon points="296,0 520,0 520,15 284,15" fill="var(--red)"/>
      </svg>
      <span class="foot-label foot-org">GUILD OF ACUTE PRACTICE MEDICINE</span>
      <span class="foot-label foot-issue">VOLUME - 01 &nbsp;|&nbsp; ISSUE - 001</span>
    </footer>
  </section>

</div>
</body>
</html>
```